Im open to ideas.. I was thinking on my business cards aswell as my logo. a place for my name. email. phone number and abn..

ive attched a file with my business logo. which i dont love the colours.. i was think a dark background with charcoal letters so something along those colour schumes but im open to ideas..

BRM Constructions

```html
<!DOCTYPE html>
<html lang="en">
<head>
<meta charset="utf-8">
<title>BRM Constructions – Business Card</title>
<link rel="stylesheet" href="https://fonts.googleapis.com/css2?family=Montserrat:wght@400;500;700;800&display=swap">
<style>
  :root {
    --page-bg: #e6e3de;
    --card-black: #0b0b0c;
    --card-sheen: #1d1d1f;
    --accent-red: #e3212b;
    --text-white: #f4f4f4;
    --text-grey: #bdbdbd;
  }
  * { box-sizing: border-box; margin: 0; padding: 0; }
  html, body {
    width: 1200px;
    height: 1022px;
    overflow: hidden;
    background: var(--page-bg);
    font-family: "Montserrat", Arial, sans-serif;
  }
  .canvas {
    position: relative;
    width: 1200px;
    height: 1022px;
  }
  .card {
    position: absolute;
    left: 320px;
    width: 560px;
    height: 320px;
    border-radius: 16px;
    background: linear-gradient(120deg, var(--card-black) 0%, var(--card-sheen) 48%, var(--card-black) 100%);
    box-shadow: 0 14px 30px rgba(0, 0, 0, 0.25);
    overflow: hidden;
  }
  .card-front { top: 151px; }
  .card-back  { top: 551px; }

  /* Front: company name */
  .brand {
    position: absolute;
    left: 0;
    right: 0;
    top: 50%;
    transform: translateY(-50%);
    display: flex;
    align-items: center;
    justify-content: center;
    gap: 16px;
  }
  .brand-square {
    width: 26px;
    height: 26px;
    background: var(--accent-red);
  }
  .brand-name {
    font-weight: 800;
    font-size: 38px;
    letter-spacing: 1px;
    color: var(--text-white);
    text-transform: uppercase;
  }

  /* Back: contact details */
  .details {
    position: absolute;
    left: 250px;
    top: 62px;
    color: var(--text-white);
  }
  .person-name {
    font-weight: 500;
    font-size: 26px;
    letter-spacing: 1px;
    color: var(--accent-red);
    text-transform: uppercase;
    line-height: 1;
  }
  .person-role {
    margin-top: 8px;
    font-size: 15px;
    color: var(--text-white);
  }
  .abn {
    margin-top: 10px;
    font-size: 15px;
  }
  .abn-label { color: var(--accent-red); font-weight: 500; }
  .contact-list {
    list-style: none;
    margin-top: 14px;
  }
  .contact-item {
    display: flex;
    align-items: center;
    gap: 10px;
    font-size: 15px;
    line-height: 1;
    margin-bottom: 11px;
  }
  .contact-icon {
    width: 13px;
    height: 13px;
    flex: none;
  }
</style>
</head>
<body>
<main class="canvas">

  <section class="card card-front" aria-label="Business card front">
    <div class="brand">
      <span class="brand-square"></span>
      <span class="brand-name">BRM Constructions</span>
    </div>
  </section>

  <section class="card card-back" aria-label="Business card back">
    <div class="details">
      <h1 class="person-name">Marcus Hale</h1>
      <p class="person-role">Director</p>
      <p class="abn"><span class="abn-label">ABN</span>: 48 216 503 719</p>
      <ul class="contact-list">
        <li class="contact-item">
          <svg class="contact-icon" viewBox="0 0 24 24" aria-hidden="true">
            <path fill="#e3212b" d="M6.6 10.8c1.4 2.8 3.8 5.1 6.6 6.6l2.2-2.2c.3-.3.7-.4 1-.2 1.1.4 2.3.6 3.6.6.6 0 1 .4 1 1V20c0 .6-.4 1-1 1C10.6 21 3 13.4 3 4c0-.6.4-1 1-1h3.5c.6 0 1 .4 1 1 0 1.3.2 2.5.6 3.6.1.3 0 .7-.2 1z"/>
          </svg>
          <span>+330 2715-8842</span>
        </li>
        <li class="contact-item">
          <svg class="contact-icon" viewBox="0 0 24 24" aria-hidden="true">
            <rect x="2" y="5" width="20" height="14" rx="1.5" fill="none" stroke="#e3212b" stroke-width="2.2"/>
            <path d="M3 6l9 7 9-7" fill="none" stroke="#e3212b" stroke-width="2.2"/>
          </svg>
          <span>info@brmconstructions.com</span>
        </li>
        <li class="contact-item">
          <svg class="contact-icon" viewBox="0 0 24 24" aria-hidden="true">
            <circle cx="12" cy="12" r="10" fill="#e3212b"/>
            <path d="M2 12h20M12 2c3 3 3 17 0 20M12 2c-3 3-3 17 0 20" fill="none" stroke="#0b0b0c" stroke-width="1.6"/>
          </svg>
          <span>www.brmconstructions.com</span>
        </li>
      </ul>
    </div>
  </section>

</main>
</body>
</html>
```